I need a letterhead for a newsletter that will go out quarterly to the dentists of the 18th district. It is called "The Crestline Digest" We are in Amarillo TX and have this landmark in the photo as our most prominent feature. If it could be used, that would be cool.
This is a professional organization newsletter so the letterhead should be somewhat professional.

Target Market(s)

Dentists

Industry/Entity Type

Dental

Font styles to use
Serif

Colors

Designer to choose only greyscale colors for use in the design.

Requirements
Must have
• I want the title of "The Crestline Digest" to be the on top with the phrase "Cobalt Ridge Dental Society" written underneath.
Nice to have
• the photo incorporated could be incorporated in black and white or color along the bottom of the letterhead or with the title inside the photo.
Should not have
• I don't want it to be cartoony. I want it to be stylish and elegant and professional.

```html
<!DOCTYPE html>
<html lang="en">
<head>
<meta charset="utf-8">
<title>The Crestline Digest – Letterhead</title>
<link rel="stylesheet" href="https://fonts.googleapis.com/css2?family=Playfair+Display:wght@900&family=Lato:wght@400;700&family=Open+Sans:wght@400;600&display=swap">
<style>
  :root {
    --brand-charcoal: #2e2e2e;
    --footer-grey: #3d3d3d;
    --swoosh-grey: #8c8c8c;
    --ink: #444444;
    --ink-dark: #222222;
    --paper: #ffffff;
    --rule: rgba(255,255,255,0.55);
  }
  * { margin: 0; padding: 0; box-sizing: border-box; }
  html, body { width: 1040px; height: 1200px; overflow: hidden; background: var(--paper); }
  .letterhead {
    position: relative;
    width: 1040px;
    height: 1200px;
    background: var(--paper);
    font-family: "Open Sans", sans-serif;
    color: var(--ink);
  }
  .masthead {
    position: absolute;
    top: 36px;
    left: 0;
    width: 100%;
    text-align: center;
  }
  .masthead__title {
    font-family: "Playfair Display", serif;
    font-weight: 900;
    font-size: 40px;
    line-height: 1;
    letter-spacing: 1px;
    text-transform: uppercase;
    color: var(--brand-charcoal);
  }
  .masthead__society {
    margin-top: 6px;
    font-family: "Lato", sans-serif;
    font-size: 17px;
    letter-spacing: 1.4px;
    text-transform: uppercase;
    color: var(--ink-dark);
  }
  .letter {
    position: absolute;
    left: 97px;
    width: 840px;
    font-size: 16px;
    line-height: 27px;
  }
  .letter__date { top: 246px; }
  .letter__recipient { top: 282px; line-height: 19px; font-style: normal; }
  .letter__greeting { top: 383px; }
  .letter__body { top: 436px; text-align: justify; hyphens: auto; }
  .letter__body p + p { margin-top: 27px; }
  .letter__closing { top: 841px; }
  .letter__signer { top: 918px; }
  .letter__signer-name { font-size: 19px; font-weight: 600; color: var(--ink-dark); line-height: 28px; }
  .letter__signer-role { font-size: 15.5px; line-height: 24px; }
  .footer-band {
    position: absolute;
    left: 0;
    bottom: 0;
    width: 1040px;
    height: 180px;
    display: block;
  }
  .footer-band__text { font-family: "Lato", sans-serif; fill: #ffffff; font-size: 19px; }
  .footer-band__label { font-weight: 700; }
</style>
</head>
<body>
<main class="letterhead">
  <header class="masthead">
    <h1 class="masthead__title">The Crestline Digest</h1>
    <p class="masthead__society">Cobalt Ridge Dental Society</p>
  </header>

  <p class="letter letter__date">Issuing Date: May 5, 2018</p>

  <address class="letter letter__recipient">
    Name Of Employee Mr. XYZABC<br>
    Address of Employee<br>
    Address Line 2 etc..
  </address>

  <p class="letter letter__greeting">Dear Mr.XYZABC</p>

  <section class="letter letter__body">
    <p>Lorem Ipsum has been the industry's standard dummy text ever since the 1500s, when an unknown printer took a galley of type and scrambled it to make a type specimen book. It has survived not only five centuries, but also the leap into electronic typesetting, remaining essentially unchanged. It was popularised in the 1960s with the release of Letraset sheets containing Lorem Ipsum passages, and more recently with desktop publishing software like Aldus PageMaker including versions of Lorem Ipsum.</p>
    <p>Lorem Ipsum is simply dummy text of the printing and typesetting industry. Lorem Ipsum has been the industry's standard dummy text ever since the 1500s, when an unknown printer took a galley of type and scrambled it to make a type specimen book.</p>
    <p>It has survived not only five centuries, but also the leap into electronic typesetting, remaining essentially unchanged. It was popularised in the 1960s with the release of Letraset sheets containing Lorem IpsumIpsum passages.</p>
  </section>

  <p class="letter letter__closing">Yours Sincerely</p>

  <div class="letter letter__signer">
    <p class="letter__signer-name">Marlon Keats</p>
    <p class="letter__signer-role">Managing Director</p>
  </div>

  <svg class="footer-band" viewBox="0 0 1040 180" xmlns="http://www.w3.org/2000/svg">
    <defs>
      <clipPath id="band-shape">
        <path d="M0,51 C60,15 120,0 200,2 C400,6 600,90 848,96 C930,98 990,80 1040,63 L1040,180 L0,180 Z"/>
      </clipPath>
      <linearGradient id="landmark-fade" x1="0" y1="0" x2="1" y2="0">
        <stop offset="0" stop-color="#9a9a9a"/>
        <stop offset="0.4" stop-color="#7a7a7a"/>
        <stop offset="1" stop-color="#3d3d3d" stop-opacity="0"/>
      </linearGradient>
      <linearGradient id="landmark-ground" x1="0" y1="0" x2="0" y2="1">
        <stop offset="0" stop-color="#b5b5b5" stop-opacity="0.5"/>
        <stop offset="0.7" stop-color="#6a6a6a" stop-opacity="0.35"/>
        <stop offset="1" stop-color="#4a4a4a" stop-opacity="0.5"/>
      </linearGradient>
    </defs>

    <path class="footer-band__swoosh" fill="var(--swoosh-grey)"
      d="M360,14 C560,40 700,70 848,72 C930,73 990,55 1040,37 L1040,50 C990,68 930,84 848,84 C700,82 560,50 360,14 Z"/>

    <path class="footer-band__wave" fill="var(--footer-grey)"
      d="M0,51 C60,15 120,0 200,2 C400,6 600,90 848,96 C930,98 990,80 1040,63 L1040,180 L0,180 Z"/>

    <g class="footer-band__photo" role="img" aria-label="Black and white photo of the canyon rock landmark under open sky, fading into the band" clip-path="url(#band-shape)">
      <rect x="0" y="0" width="400" height="180" fill="url(#landmark-fade)"/>
      <rect x="0" y="0" width="300" height="180" fill="url(#landmark-ground)" opacity="0.8"/>
    </g>

    <text class="footer-band__text" x="312" y="125">218 Mesa Court,&#160; 45452 Country Name</text>
    <line x1="312" y1="134" x2="928" y2="134" stroke="var(--rule)" stroke-width="1"/>
    <text class="footer-band__text" x="928" y="160" text-anchor="end"><tspan class="footer-band__label">P:</tspan> 044-555 017 342 <tspan class="footer-band__label">| E:</tspan> office@crestlinedigest.org <tspan class="footer-band__label">| www.crestlinedigest.org</tspan></text>
  </svg>
</main>
</body>
</html>
```